Harrowmere Freight, Project

Company Profile
Harrowmere Freight Sdn Bhd is a well established and experienced freight forwarder in Kuala Lumpur, Malaysia. We specialize in air and sea forwarding, Custom Brokerage and regulatory compliance services, inland transportation,
overseas freighting and warehousing and distribution management. With our dedicated qualified and experienced professionals, we are fully committed to serving our clients.

Our Mission
Based on the motto “Quick, Reliable and Polite”, Harrowmere Freight is dedicated to upholding the following three points corporate philosophy:
1. Adhering to the principle that “the customer always comes first”.
2. Contributing to the development of the local community.
3. Making it our duty to be responsible and sincere.

Our Edge
• One-Stop Logistics Solutions
• Extensive Network Throughout Malaysia
• Highly Qualified and Experienced Pool of Professionals
• Comprehensive IT Solutions
• Innovative and Customer-focused Solutions
• Flexible and Consistent in Managing Exceptions
• Total Supply Chain Visibility

Target Market(s)

We sell the logistics services to all the industry in Malaysia. (ONE Stop Logistics Solutions)

Industry/Entity Type

Logistic

Contact Information for Business Card

I want the back of the card to be white with the logo and slogan. i would like to see the logo on the front with the general info.

Requirements
Must have
• Name, Title, Office, Cell, Fax, Email, Address, Website
Nice to have
• Modern Design Business Card

```html
<!DOCTYPE html>
<html lang="en">
<head>
<meta charset="utf-8">
<title>Harrowmere Freight Stationery</title>
<link href="https://fonts.googleapis.com/css2?family=Roboto:wght@400;500;700&family=Roboto+Condensed:wght@700&display=swap" rel="stylesheet">
<style>
:root{
  --bg:#cccccc;
  --paper:#f7f7f7;
  --dark:#36322f;
  --blue:#2f66a3;
  --blue-light:#3a96d5;
  --text:#3b3b3b;
  --white:#ffffff;
}
*{box-sizing:border-box;margin:0;padding:0}
html,body{width:1198px;height:1200px;overflow:hidden}
body{background:var(--bg);position:relative;font-family:"Roboto",sans-serif;color:var(--text)}
.sheet{position:absolute;background:var(--paper);box-shadow:0 1px 4px rgba(0,0,0,.25);overflow:hidden}
.wave{position:absolute;left:0;top:0;width:100%}

/* brand name: stacked in two lines, one colour, one weight */
.brand{position:absolute;font-family:"Roboto",sans-serif;font-weight:500;color:var(--blue);white-space:nowrap;display:flex;align-items:center;gap:5px;line-height:1.05}
.brand .dot{display:inline-block;border-radius:50%;background:currentColor;flex:none}
.brand .words{display:block}

/* letterhead */
.letterhead{left:89px;top:49px;width:484px;height:686px}
.letterhead .company{position:absolute;right:26px;top:22px;text-align:right;color:var(--white)}
.company .name{font-family:"Roboto Condensed",sans-serif;font-weight:700;font-size:10px;letter-spacing:.2px}
.company .reg{font-size:6.5px;margin-top:2px}
.company .contacts{margin-top:10px;font-size:6px;line-height:9px}
.letterhead .brand{left:28px;top:112px;font-size:15px}
.letterhead .brand .dot{width:9px;height:9px}
.address{position:absolute;font-size:6.5px;line-height:10px;color:var(--text);white-space:nowrap}
.letterhead .address{left:28px;top:627px}
.slogan-band{position:absolute;right:0;background:var(--blue);color:var(--white);font-weight:700;font-size:6.5px;letter-spacing:.3px;display:flex;align-items:center;white-space:nowrap;clip-path:polygon(10% 0,100% 0,100% 100%,0 100%)}
.letterhead .slogan-band{top:630px;width:216px;height:25px;padding-left:47px}

/* folder */
.folder{left:625px;top:49px;width:485px;height:686px;background:linear-gradient(180deg,var(--blue-light) 0%,#3274b6 55%,var(--blue) 100%)}
.folder .spine{position:absolute;top:0;bottom:0;width:1px;background:rgba(20,60,120,.55)}
.folder .brand{left:0;right:0;top:340px;justify-content:center;color:var(--white);font-size:30px}
.folder .brand .dot{width:16px;height:16px}

/* envelopes */
.env-back{left:170px;top:773px;width:587px;height:264px}
.env-back .flap{position:absolute;left:0;top:0;width:100%;height:90px}
.env-back .web{position:absolute;left:0;right:0;top:44px;text-align:center;font-size:7px;letter-spacing:.6px;color:#dfe8f3}
.env-front{left:121px;top:885px;width:586px;height:265px}
.env-front .tag{position:absolute;right:28px;top:28px;color:var(--white);font-weight:700;font-size:7px}
.env-front .brand{left:28px;top:210px;font-size:13px}
.env-front .brand .dot{width:8px;height:8px}
.env-front .address{left:140px;top:212px}

/* business cards */
.card{width:210px;height:127px;left:868px}
.card-services{top:797px}
.card-contact{top:963px}
.card .tag{position:absolute;right:10px;top:12px;color:var(--white);font-family:"Roboto Condensed",sans-serif;font-weight:700;font-size:5.5px}
.card .co{position:absolute;left:10px;top:29px;font-family:"Roboto Condensed",sans-serif;font-weight:700;font-size:5.5px;color:var(--blue)}
.card .list{position:absolute;left:10px;top:38px;list-style:none;font-size:4.3px;line-height:7.8px;white-space:nowrap}
.card .list li::before{content:"» ";color:var(--blue)}
.card .brand{right:12px;font-size:9px;text-align:right}
.card .brand .dot{width:5px;height:5px}
.card-services .brand{top:80px}
.card-contact .brand{top:88px}
.card .slogan-band{bottom:2px;height:13px;width:124px;font-size:4.8px;padding-left:24px}
.card-contact .slogan-band{left:0;right:auto;width:124px;padding-left:12px;clip-path:polygon(0 0,90% 0,100% 100%,0 100%)}
.card .person{position:absolute;right:10px;top:9px;text-align:right;color:var(--white)}
.person .pname{font-weight:700;font-size:6.5px}
.person .ptitle{font-size:3.8px}
.person .pcell{font-weight:700;font-size:4.5px}
.card .reg{position:absolute;left:10px;top:38px;font-size:4px}
.card .caddr{position:absolute;left:10px;top:51px;font-size:4.3px;line-height:7px;white-space:nowrap}
.card .cinfo{position:absolute;left:10px;top:76px;list-style:none;font-size:4.3px;line-height:7px;white-space:nowrap}
.card .cinfo li::before{content:"■ ";color:var(--blue);font-size:3px}
</style>
</head>
<body>

<section class="sheet letterhead">
  <svg class="wave" viewBox="0 0 484 140" aria-hidden="true">
    <path fill="#36322f" d="M0,0H484V114C410,114 350,96 280,62C200,22 100,6 0,24Z"/>
    <path fill="#2f66a3" d="M0,54C90,26 190,22 280,70C350,108 420,128 484,128V120C420,120 350,100 280,62C190,18 90,20 0,46Z"/>
  </svg>
  <div class="company">
    <div class="name">HARROWMERE FREIGHT SDN. BHD.</div>
    <div class="reg">(Company No. 2048613-K)</div>
    <div class="contacts">aiman.rashid@harrowmere.com.my ☎<br>(603) 5521 6830 / 6840 ☏<br>(603) 5521 6850 ✉<br>harrowmere.com.my ◍</div>
  </div>
  <div class="brand"><span class="dot"></span><span class="words">Harrowmere<br>Freight</span></div>
  <p class="address">No. 14B, 2nd Floor, Jalan Seroja 3,<br>Taman Seroja Indah, 41050 Klang,<br>Selangor Darul Ehsan, Malaysia.</p>
  <div class="slogan-band">ONE STOP LOGISTICS SOLUTIONS</div>
</section>

<section class="sheet folder">
  <span class="spine" style="left:33px"></span>
  <span class="spine" style="left:40px"></span>
  <div class="brand"><span class="dot"></span><span class="words">Harrowmere<br>Freight</span></div>
</section>

<section class="sheet env-back">
  <svg class="flap" viewBox="0 0 587 90" preserveAspectRatio="none" aria-hidden="true">
    <path fill="#2f66a3" d="M6,0H587L552,60C540,82 530,88 510,88H70C50,88 42,80 32,62Z"/>
  </svg>
  <div class="web">www.harrowmere.com.my</div>
</section>

<section class="sheet env-front">
  <svg class="wave" viewBox="0 0 586 110" aria-hidden="true">
    <path fill="#36322f" d="M0,0H586V82C500,80 430,60 350,36C260,10 120,4 0,26Z"/>
    <path fill="#2f66a3" d="M0,62C110,28 250,30 360,62C440,86 510,92 586,92V84C510,84 440,76 360,52C250,20 110,20 0,52Z"/>
  </svg>
  <div class="tag">ONE STOP LOGISTICS SOLUTIONS</div>
  <div class="brand"><span class="dot"></span><span class="words">Harrowmere<br>Freight</span></div>
  <p class="address">No. 14B, 2nd Floor, Jalan Seroja 3,<br>Taman Seroja Indah, 41050 Klang,<br>Selangor Darul Ehsan, Malaysia.</p>
</section>

<section class="sheet card card-services">
  <svg class="wave" viewBox="0 0 210 44" aria-hidden="true">
    <path fill="#2f66a3" d="M0,0H210V38C180,38 150,28 120,16C80,2 40,2 0,12Z"/>
    <path fill="#ffffff" d="M0,14C40,4 80,4 120,18C150,30 180,38 210,38V42C180,42 150,34 120,22C80,8 40,8 0,18Z"/>
    <path fill="#36322f" d="M0,12C40,2 80,2 120,16C110,10 80,6 60,6C40,6 20,8 0,14Z"/>
  </svg>
  <div class="tag">We're Specialize In</div>
  <div class="co">HARROWMERE FREIGHT SDN. BHD.</div>
  <ul class="list">
    <li>International Shipping (Air / Sea)</li>
    <li>Consolidation NVOCC</li>
    <li>Project Management</li>
    <li>Supply Chain Management</li>
    <li>Tax Exemption Consultancy</li>
    <li>Custom Brokerage</li>
    <li>Transportation / Haulage</li>
    <li>Warehousing</li>
    <li>Packing &nbsp;» Marine Insurance</li>
    <li>Distribution &nbsp;» Door to Door</li>
  </ul>
  <div class="brand"><span class="dot"></span><span class="words">Harrowmere<br>Freight</span></div>
  <div class="slogan-band">ONE STOP LOGISTICS SOLUTIONS</div>
</section>

<section class="sheet card card-contact">
  <svg class="wave" viewBox="0 0 210 44" aria-hidden="true">
    <path fill="#2f66a3" d="M0,0H210V44C180,44 150,34 120,22C80,6 40,6 0,16Z"/>
    <path fill="#ffffff" d="M0,16C40,6 80,6 120,22C150,34 180,42 210,42V46H0Z"/>
    <path fill="#36322f" d="M0,16C40,6 80,6 120,22C104,14 80,10 60,10C40,10 20,12 0,20Z"/>
  </svg>
  <div class="person">
    <div class="pname">Aiman Rashid</div>
    <div class="ptitle">Managing Director</div>
    <div class="pcell">+6012-418 2275 ✆</div>
  </div>
  <div class="co">HARROWMERE FREIGHT SDN. BHD.</div>
  <div class="reg">(Company No. 2048613-K)</div>
  <p class="caddr">No. 14B, 2nd Floor, Jalan Seroja 3,<br>Taman Seroja Indah, 41050 Klang,<br>Selangor Darul Ehsan, Malaysia.</p>
  <ul class="cinfo">
    <li>(603) 5521 6830 / 6840</li>
    <li>(603) 5521 6850</li>
    <li>aiman.rashid@harrowmere.com.my</li>
    <li>www.harrowmere.com.my</li>
  </ul>
  <div class="brand"><span class="dot"></span><span class="words">Harrowmere<br>Freight</span></div>
  <div class="slogan-band">ONE STOP LOGISTICS SOLUTIONS</div>
</section>

</body>
</html>
```